Logo + Label Design (Men’s Grooming Brand & Product Packaging)

Design a logo and 2 oz pomade label for Brel, a modern men’s grooming brand focused on clean, high-quality, natural ingredients. The design should establish a bold, masculine, minimalist identity that can later extend to products like shaving gel and body wash.

Key Requirements

Create a primary logo for “Brel” and a core label for the 2 oz pomade jar (screw-top).

Use a clean, modern style — masculine, confident, and approachable (think Dorran’s, Velta, Northfield Kit).

Design for 1–2 color screen printing on solid jar colors (white, black, or navy).

Avoid gradients, foil, or embossing. Must work in black & white.

Provide: vector logo, mockup of the 2 oz jar, color palette (CMYK/RGB/HEX), and font specs.

Winning design may lead to future projects (body wash, shave gel, skincare lines).

Font styles to use
Other font styles liked:
• We like the fonts and design concept in the attached mockup.

Requirements
Should not have
• We want to avoid too much writing or busy designs. We want to avoid having graphics/illustrations embedded in the logo if they will cause the brand to look less classy or sophisticated. We also want the design to look simple and all-American (e.g. Hollister and Vane, Pine Ledger, The KIM, etc). We’d like to give a Pellham & Royce vibe that feels classy and high end.

```html
<!DOCTYPE html>
<html lang="en">
<head>
<meta charset="utf-8">
<title>Brel Men's Hair Pomade – Label</title>
<link href="https://fonts.googleapis.com/css2?family=Libre+Caslon+Text:wght@700&family=Josefin+Sans:wght@400;600&family=Archivo+Narrow:wght@500&display=swap" rel="stylesheet">
<style>
  :root{
    --cream:#f1f0e2;
    --ink:#0b0b0b;
    --paper:#ffffff;
  }
  *{box-sizing:border-box;margin:0;padding:0}
  html,body{width:1200px;height:1200px;overflow:hidden}
  body{background:var(--cream);position:relative;color:var(--paper)}

  /* Wrap-around jar label */
  .wrap-label{position:absolute;left:25px;top:330px;width:1150px;height:136px}
  .wrap-label .rule-outer{position:absolute;left:0;right:0;height:4px;background:var(--ink)}
  .wrap-label .rule-outer.top{top:0}
  .wrap-label .rule-outer.bottom{bottom:0}
  .wrap-label .band{position:absolute;left:0;right:0;top:8px;bottom:8px;background:var(--ink)}
  .wrap-label .band::before,.wrap-label .band::after{content:"";position:absolute;left:0;right:0;height:2px;background:var(--paper)}
  .wrap-label .band::before{top:6px}
  .wrap-label .band::after{bottom:6px}

  .directions{position:absolute;left:10px;top:19px;width:428px;font-family:"Josefin Sans",sans-serif;font-size:13.2px;line-height:15.6px;text-align:justify;letter-spacing:.2px}
  .directions .head{display:block;text-align:left}

  .brand-lockup{position:absolute;left:470px;top:8px;width:210px;text-align:center}
  .wordmark{font-family:"Libre Caslon Text",serif;font-weight:700;font-size:52px;line-height:54px;letter-spacing:1px}
  .product-name{font-family:"Josefin Sans",sans-serif;font-weight:600;font-size:14px;letter-spacing:2.2px;margin-top:2px}
  .tagline{display:flex;align-items:center;justify-content:center;gap:7px;font-family:"Josefin Sans",sans-serif;font-size:11.5px;letter-spacing:1.8px;margin-top:5px}
  .tagline .dash{width:30px;height:1.5px;background:var(--paper)}
  .net-weight{display:inline-block;background:var(--paper);color:var(--ink);font-family:"Josefin Sans",sans-serif;font-size:9px;padding:2px 4px 0;margin-top:6px;letter-spacing:.4px}

  .claims{position:absolute;left:718px;top:25px;width:250px;font-family:"Archivo Narrow",sans-serif;font-size:8.6px;line-height:11px;letter-spacing:.1px}
  .claims ul{list-style:none}
  .claims li::before{content:"• "}
  .maker{margin-top:9px;font-size:10px;line-height:12px}

  .ingredients{position:absolute;left:970px;top:25px;width:170px;font-family:"Archivo Narrow",sans-serif;font-size:7.2px;line-height:11px;text-align:justify}

  /* Lid label */
  .lid-label{position:absolute;left:420px;top:590px;width:360px;height:360px}
  .lid-label svg{position:absolute;inset:0}
  .lid-content{position:absolute;inset:0;text-align:center;padding-top:66px}
  .lid-content .wordmark{font-size:80px;line-height:80px}
  .lid-content .product-name{font-size:19px;letter-spacing:3px;margin-top:10px}
  .lid-content .tagline{font-size:16px;letter-spacing:2.4px;margin-top:12px;gap:10px}
  .lid-content .tagline .dash{width:56px;height:2px}
  .lid-claims{margin-top:22px;font-family:"Josefin Sans",sans-serif;font-size:6.8px;line-height:16px;letter-spacing:.9px}
  .lid-content .net-weight{font-size:12px;padding:3px 6px 1px;margin-top:22px}
</style>
</head>
<body>

<section class="wrap-label" aria-label="Jar wrap label">
  <div class="rule-outer top"></div>
  <div class="band">
    <p class="directions"><span class="head">DIRECTIONS:</span>MELT SMALL AMOUNT OF POMADE BETWEEN HANDS BEFORE MASSAGING INTO DAMP HAIR (FOR SLEEKER LOOK) OR DRY HAIR (FOR MORE TEXTURE). STYLE AS DESIRED. FOR EXTERNAL USE ONLY. AVOID CONTACT WITH EYES. IF IRRITATION OCCURS, DISCONTINUE USE.</p>

    <div class="brand-lockup">
      <div class="wordmark">BREL</div>
      <div class="product-name">MEN’S HAIR POMADE</div>
      <div class="tagline"><span class="dash"></span>FRESH &amp; CLEAN<span class="dash"></span></div>
      <span class="net-weight">2 OZ (57 G)</span>
    </div>

    <div class="claims">
      <ul>
        <li>NATURALLY DERIVED PLANT &amp; BEE-BASED INGREDIENTS</li>
        <li>ALCOHOL FREE, NON-IRRITATING</li>
        <li>FORMULATED TO MINIMIZE SCALP IRRITATION</li>
      </ul>
      <p class="maker">MANUFACTURED BY:<br>BREL HEALTH PRODUCTS, ASHFORD, NC 28990<br>VISIT US AT BRELHEALTHPRODUCTS.COM</p>
    </div>

    <p class="ingredients">INGREDIENTS:<br>BUTYROSPERMUM PARKII (SHEA BUTTER), CERA ALBA (BEESWAX), POLYGLYCEROL-3 BEESWAX (CERA BELLINA), CAPRYLIC/CAPRIC TRIGLYCERIDE (FRACTIONATED COCONUT OIL), TOCOPHEROL (VITAMIN E), FRAGRANCE (PARFUM)</p>
  </div>
  <div class="rule-outer bottom"></div>
</section>

<section class="lid-label" aria-label="Jar lid label">
  <svg viewBox="0 0 360 360" width="360" height="360" aria-hidden="true">
    <circle cx="180" cy="180" r="180" fill="var(--ink)"/>
    <circle cx="180" cy="180" r="166" fill="none" stroke="var(--paper)" stroke-width="2.5"/>
  </svg>
  <div class="lid-content">
    <div class="wordmark">BREL</div>
    <div class="product-name">MEN’S HAIR POMADE</div>
    <div class="tagline"><span class="dash"></span>FRESH &amp; CLEAN<span class="dash"></span></div>
    <div class="lid-claims">NATURALLY DERIVED PLANT &amp; BEE-BASED INGREDIENTS<br>ALCOHOL FREE, NON-IRRITATING<br>FORMULATED TO MINIMIZE SCALP IRRITATION</div>
    <span class="net-weight">2 OZ (57 G)</span>
  </div>
</section>

</body>
</html>
```